Rebrand & reskin fitbrisko.com (Uncoded)

Fitbrisko.com is a commerce website and app for sports and fitness classes and events. In order to improve its appeal, we invite designers to provide their 'skins' for the landing page, club page and event page. Designers can propose using alternate controls and layouts for these pages, and comment on ways to improve the site's usability. It must remain easy to use on a portrait mobile phone screen, responsive design where necessary to also provide a good experience on desktop.

Please navigate to fitbrisko.com and explore the site, and we look forwards to your suggestions!

Target Market(s)

Primary: Tech-savvy mobile users. Secondary: Desktop users

Industry/Entity Type

Health And Wellness

Number of Pages Required

3 page

Font styles to use
Sans Serif

Colors
ffffff
f37122

Requirements
Must have
• This brief is all about changing the look and feel of the site; the winning design will have an immediate 'wow' factor, yet not sacrifice the ease of finding and paying for classes. It must retain the logo, white and orange must be the primary colours used.
Should not have
• The colour palette must remain roughly as is; for example, a very dark site will not appeal.

```html
<!DOCTYPE html>
<html lang="en">
<head>
<meta charset="utf-8">
<title>Fitbrisko – Events</title>
<link rel="stylesheet" href="https://fonts.googleapis.com/css2?family=Open+Sans:wght@400;600&family=Roboto:wght@400;500&display=swap">
<style>
  :root {
    --orange: #f37122;
    --orange-dark: #e35f14;
    --white: #ffffff;
    --page-bg: #ececec;
    --sidebar: #474751;
    --sidebar-line: #5d5d67;
    --tab-top: #4d4d55;
    --tab-bottom: #2f2f33;
    --footer: #2f2f31;
    --text-dark: #3a3a3e;
    --text-body: #8a8a8e;
    --nav-text: #444448;
    --rule: #dcdcdc;
  }
  * { box-sizing: border-box; margin: 0; padding: 0; }
  html, body { width: 1200px; height: 928px; overflow: hidden; }
  body {
    position: relative;
    font-family: "Open Sans", Arial, sans-serif;
    background: linear-gradient(135deg, #f1f1f1 0%, #e8e8e8 50%, #efefef 100%);
  }

  /* Header */
  .site-header {
    position: absolute; left: 0; top: 0; width: 1200px; height: 103px;
    background: var(--white); border-bottom: 1px solid var(--rule);
  }
  .brand {
    position: absolute; left: 117px; top: 34px;
    display: flex; align-items: center; gap: 10px;
    font-family: "Roboto", Arial, sans-serif; font-weight: 500;
    font-size: 27px; letter-spacing: 1px; color: var(--orange);
  }
  .brand-dot { width: 32px; height: 32px; border-radius: 50%; background: var(--orange); }
  .main-nav { position: absolute; left: 423px; top: 0; height: 102px; display: flex; }
  .main-nav a {
    display: flex; align-items: center; justify-content: center;
    height: 102px; text-decoration: none;
    font-family: "Roboto", Arial, sans-serif; font-size: 17px; letter-spacing: .4px;
    color: var(--nav-text); border-right: 1px solid var(--rule);
  }
  .main-nav a:first-child { border-right-color: var(--rule); }
  .nav-calendar { width: 152px; }
  .nav-feed { width: 110px; }
  .nav-nearby { width: 142px; }
  .nav-classes { width: 140px; }
  .nav-event {
    width: 114px; color: var(--white) !important; border-right: none !important;
    background: linear-gradient(#2f2f31, #3f3f43);
  }

  /* Sidebar */
  .sidebar {
    position: absolute; left: 105px; top: 103px; width: 223px; height: 766px;
    background: var(--sidebar);
  }
  .side-item {
    display: flex; align-items: center; height: 57px;
    border-bottom: 1px solid var(--sidebar-line);
    color: var(--white); text-decoration: none;
    font-family: "Roboto", Arial, sans-serif; font-weight: 500; font-size: 16.5px; letter-spacing: .3px;
  }
  .side-item:last-child { border-bottom: none; }
  .side-icon { width: 68px; display: flex; justify-content: center; }

  /* Content */
  .page-title {
    position: absolute; left: 366px; top: 142px;
    font-family: "Roboto", Arial, sans-serif; font-weight: 400;
    font-size: 31px; letter-spacing: 1px; color: var(--text-dark);
  }
  .event-tabs { position: absolute; left: 364px; top: 206px; width: 211px; list-style: none; z-index: 2; }
  .event-tab {
    position: relative; height: 42px; margin-bottom: 1px;
    padding-left: 20px; display: flex; align-items: center;
    font-family: "Roboto", Arial, sans-serif; font-size: 16px; color: var(--white);
    background: linear-gradient(var(--tab-top), var(--tab-bottom));
  }
  .event-tab.is-active { background: linear-gradient(var(--orange), var(--orange-dark)); }
  .event-tab.is-active::after {
    content: ""; position: absolute; right: -10px; top: 50%; transform: translateY(-50%);
    border-left: 10px solid var(--orange); border-top: 9px solid transparent; border-bottom: 9px solid transparent;
  }
  .event-card {
    position: absolute; left: 575px; top: 205px; width: 516px; height: 371px;
    background: var(--white); border: 1px solid var(--rule);
  }
  .event-date { position: absolute; left: 30px; top: 42px; font-size: 13px; color: var(--text-dark); }
  .event-heading {
    position: absolute; left: 29px; top: 62px;
    font-size: 17px; font-weight: 400; letter-spacing: .3px; color: var(--orange);
  }
  .event-text {
    position: absolute; left: 29px; width: 290px;
    font-size: 12.7px; line-height: 21px; color: var(--text-body);
  }
  .event-text.first { top: 90px; }
  .event-text.second { top: 187px; }
  .event-photo {
    position: absolute; left: 333px; top: 33px; width: 158px; height: 158px; border-radius: 50%;
    background: radial-gradient(circle at 40% 35%, #b9c48a 0%, #7f9a4e 45%, #5d6f6a 100%);
  }

  /* Footer */
  .site-footer {
    position: absolute; left: 0; top: 869px; width: 1200px; height: 59px;
    background: var(--footer); display: flex; align-items: center; justify-content: center;
    font-size: 14px; color: #a9a9ad;
  }
</style>
</head>
<body>
  <header class="site-header">
    <div class="brand"><span class="brand-dot"></span>FITBRISKO</div>
    <nav class="main-nav">
      <a class="nav-calendar" href="#">CALENDAR</a>
      <a class="nav-feed" href="#">FEED</a>
      <a class="nav-nearby" href="#">NEAR BY</a>
      <a class="nav-classes" href="#">CLASSES</a>
      <a class="nav-event" href="#">EVENT</a>
    </nav>
  </header>

  <aside class="sidebar">
    <a class="side-item" href="#">
      <span class="side-icon">
        <svg width="26" height="22" viewBox="0 0 26 22" fill="none" stroke="#fff" stroke-width="2.4">
          <path d="M15 2h7a2 2 0 0 1 2 2v14a2 2 0 0 1-2 2h-7"/>
          <path d="M2 8h7V4l7 7-7 7v-4H2z" fill="#fff" stroke="none"/>
        </svg>
      </span>LOGIN
    </a>
    <a class="side-item" href="#">
      <span class="side-icon">
        <svg width="24" height="28" viewBox="0 0 24 28" fill="none" stroke="#fff" stroke-width="2">
          <rect x="2" y="3" width="20" height="23" rx="2"/>
          <path d="M8 1v5M16 1v5"/>
          <path d="M15 14l1 2.6 2.6.2-2 1.7.7 2.6L15 19.6l-2.3 1.5.7-2.6-2-1.7 2.6-.2z" fill="#fff" stroke="none"/>
        </svg>
      </span>MY DIARY
    </a>
    <a class="side-item" href="#">
      <span class="side-icon">
        <svg width="34" height="34" viewBox="0 0 34 34">
          <rect x="7" y="7" width="20" height="20" transform="rotate(45 17 17)" fill="#fff"/>
          <path d="M9 15h3v4H9zM12 13h3v8h-3zM19 13h3v8h-3zM22 15h3v4h-3zM15 16h4v2h-4z" fill="#474751"/>
        </svg>
      </span>MY CLUBS
    </a>
    <a class="side-item" href="#">
      <span class="side-icon">
        <svg width="26" height="28" viewBox="0 0 26 28" fill="#fff">
          <circle cx="13" cy="8" r="7"/>
          <path d="M1 28v-5a7 7 0 0 1 7-7h10a7 7 0 0 1 7 7v5z"/>
        </svg>
      </span>MY PROFILE
    </a>
  </aside>

  <main>
    <h1 class="page-title">EVENTS</h1>
    <ul class="event-tabs">
      <li class="event-tab is-active">1st Event Tittle here</li>
      <li class="event-tab">2nd Event Tittle here</li>
      <li class="event-tab">3rd Event Tittle here</li>
      <li class="event-tab">4th Event Tittle here</li>
      <li class="event-tab">5th Event Tittle here</li>
    </ul>
    <article class="event-card">
      <p class="event-date">25 Aug 2016</p>
      <h2 class="event-heading">Proin nulla arcu nonummy luctus</h2>
      <p class="event-text first">Praesent sit amet est In dictum dolor eu dictum porttitor enim felis viverra mi eget luctus massa purus quis odio Etiam nulla massa pharetra facilisis volutpat in imperdiet sit</p>
      <p class="event-text second">interdum vel blandit sed nulla In ullamcorper est eget tempor cursus neque mi consectetuer mi a ultricies massa est sed nisl Class aptent taciti sociosqu ad litora torquent per conubia nostra per inceptos hymenaeos</p>
      <div class="event-photo" role="img" aria-label="Photo of a smiling runner crossing the finish line outdoors"></div>
    </article>
  </main>

  <footer class="site-footer">© 2016 Company Name&nbsp; All right reserved&nbsp; Term of Use</footer>
</body>
</html>
```